Client Meeting and installation Email Follow up

I would like a follow-up email template created.
Currently, we do a lot of new construction builds and meet with clients about 6-3 months before they take possession of their new house. I want a follow-up email template to be sent after the homeowner takes possession of their house that enquires if the clients are happy about their new lighting, the service they received, and their customer service representative with Brightwell Lamps and Breezes. I have attached a few files of what our current marketing looks like.
Target Market(s)
Home Owners We have already met with
Industry/Entity Type
Residential lighting
Font styles to use
Other font styles liked:
- Alta Light, Playfair Display, Montserrat
Colors
Designer to choose colors to be used in the design.
Look and feel
Each slider illustrates characteristics of the customer's brand and the style your logo design should communicate.

```html
<!DOCTYPE html>
<html lang="en">
<head>
<meta charset="utf-8">
<title>Brightwell Lamps and Breezes – Your New Lighting and Installation Experience</title>
<link rel="stylesheet" href="https://fonts.googleapis.com/css2?family=Bitter:wght@600;700&family=Montserrat:wght@600&display=swap">
<style>
  :root {
    --tan: #dfc4a6;
    --tan-dark: #a48e6e;
    --frame: #a08a72;
    --ink: #111111;
    --white: #ffffff;
    --footer: #000000;
  }
  * { margin: 0; padding: 0; box-sizing: border-box; }
  html, body { width: 1200px; height: 4078px; overflow: hidden; background: var(--white); }
  .email { position: relative; width: 1200px; height: 4078px; overflow: hidden; background: var(--white); }
  .abs { position: absolute; }

  .hero-photo {
    left: 0; top: 0; width: 1200px; height: 833px;
    background: linear-gradient(180deg, #eef0f2 0%, #dfe2e6 35%, #b89a74 62%, #3a3c48 82%, #4a5572 100%);
  }

  .brand {
    left: 0; width: 1200px; display: flex; justify-content: center; align-items: center; gap: 20px;
    font-family: "Bitter", serif; font-weight: 700; font-size: 52px; color: var(--ink); letter-spacing: 0.5px;
  }
  .brand-mark { width: 30px; height: 30px; background: var(--ink); }
  .brand--top { top: 880px; height: 140px; }
  .brand--bottom { top: 3755px; height: 140px; }

  .headline {
    left: 0; top: 1073px; width: 1200px; text-align: center;
    font-family: "Bitter", serif; font-weight: 700; font-size: 50px; line-height: 62px; color: var(--tan-dark);
  }

  .frame { border: 3px solid var(--frame); }
  .room-photo { background: linear-gradient(160deg, #f2f2f2, #cfd3d8); }
  .room-photo--dining { background: linear-gradient(180deg, #6f7e93 0%, #7b8aa0 55%, #a9794e 78%, #c09a72 100%); }
  .room-photo--kitchen { background: linear-gradient(180deg, #e6e6e6 0%, #f4f4f4 45%, #fafafa 75%, #cfcfcf 100%); }
  .room-photo--island { background: linear-gradient(180deg, #ededed 0%, #f6f6f6 40%, #caa67c 70%, #d9d5ce 100%); }

  .card { background: var(--tan); color: var(--white); }
  .card-title {
    position: absolute; font-family: "Bitter", serif; font-weight: 600; font-size: 48px; line-height: 56px; white-space: nowrap;
  }
  .card-rule { position: absolute; width: 111px; height: 3px; background: var(--ink); }
  .card-text {
    position: absolute; font-family: "Montserrat", sans-serif; font-weight: 600; font-size: 23px; line-height: 40px;
  }

  .fixture { background: radial-gradient(ellipse at center, #e6e6e6 0%, #f4f4f4 55%, #ffffff 80%); }

  .footer {
    left: 0; top: 3965px; width: 1200px; height: 113px; background: var(--footer);
    display: flex; align-items: center; justify-content: center;
    font-family: "Montserrat", sans-serif; font-weight: 600; font-size: 24px; letter-spacing: 0.5px; color: var(--white);
  }
</style>
</head>
<body>
<div class="email">
  <div class="abs hero-photo" role="img" aria-label="Bright kitchen with a crystal chandelier above a wooden dining table and dark upholstered chairs"></div>

  <div class="abs brand brand--top"><span class="brand-mark"></span><span>Brightwell Lamps and Breezes</span></div>

  <h1 class="abs headline">Your New Lighting and Installation<br>Experience</h1>

  <!-- New lighting -->
  <div class="abs frame" style="left:59px; top:1350px; width:463px; height:567px;"></div>
  <div class="abs room-photo room-photo--dining" style="left:92px; top:1306px; width:457px; height:573px;" role="img" aria-label="Dining nook with a brushed nickel chandelier, blue chairs and tulips on a wooden table"></div>
  <div class="abs card" style="left:461px; top:1439px; width:739px; height:320px;">
    <h2 class="card-title" style="left:63px; top:70px;">New Lighting?</h2>
    <div class="card-rule" style="left:66px; top:137px;"></div>
    <p class="card-text" style="left:63px; top:170px;">We hope it’s adding the perfect<br>ambiance to your new home.</p>
  </div>
  <div class="abs fixture" style="left:926px; top:1757px; width:253px; height:246px;" role="img" aria-label="Three-light chandelier with white globe shades"></div>

  <!-- Installation process -->
  <div class="abs frame" style="left:682px; top:2167px; width:464px; height:567px;"></div>
  <div class="abs room-photo room-photo--kitchen" style="left:657px; top:2123px; width:457px; height:573px;" role="img" aria-label="White kitchen with three slim pendant lights over the counter"></div>
  <div class="abs card" style="left:0; top:2257px; width:746px; height:319px;">
    <h2 class="card-title" style="left:114px; top:71px;">Installation Process?</h2>
    <div class="card-rule" style="left:116px; top:135px;"></div>
    <p class="card-text" style="left:114px; top:169px;">Your feedback helps us ensure we’re<br>delivering the best possible experience.</p>
  </div>
  <div class="abs fixture" style="left:32px; top:2576px; width:253px; height:221px;" role="img" aria-label="Three-light chandelier with white globe shades"></div>

  <!-- Customer service -->
  <div class="abs frame" style="left:59px; top:2990px; width:463px; height:567px;"></div>
  <div class="abs room-photo room-photo--island" style="left:92px; top:2946px; width:457px; height:573px;" role="img" aria-label="Kitchen island with three glass pendants and wooden bar stools"></div>
  <div class="abs card" style="left:461px; top:3080px; width:739px; height:319px;">
    <h2 class="card-title" style="left:64px; top:58px;">Customer Service</h2>
    <div class="card-rule" style="left:66px; top:124px;"></div>
    <p class="card-text" style="left:63px; top:153px;">If there’s anything we can improve or if there’s a<br>particular aspect you appreciated, please let<br>us know.</p>
  </div>
  <div class="abs fixture" style="left:902px; top:3399px; width:254px; height:226px;" role="img" aria-label="Three-light chandelier with white globe shades"></div>

  <div class="abs brand brand--bottom"><span class="brand-mark"></span><span>Brightwell Lamps and Breezes</span></div>

  <div class="abs footer">WWW.BRIGHTWELLLAMPS.COM</div>
</div>
</body>
</html>
```